Buch-/E-Book-Cover im Bereich der Persönlichkeitsentwicklung
Vielen lieben Dank für die super Arbeit von Dir. Das Design ist klasse und die vielen Vorschläge waren auch super. Die komplette Zusammenarbeit verlief sehr professionell und Änderungswünsche wurden sehr schnell umgesetzt. Ich kann Dich voll und ganz weiterempfehlen.
Zielgruppe
Wir arbeiten in der Persönlichkeitsentwicklung für Jugendliche. Dabei spezialisieren wir uns auf den Altersbereich 12 - 17 Jahre. Unser Ziel ist es jungen Menschen zu zeigen, wie Sie zu sich selbst finden und ein glückliches sowie erfolgreiches Leben führen können.
Aufgabenstellung
- Das Design sollte für die Eltern von Teenagern und auch für die Teenager selbst ausgelegt werden. Das Buch ist für die Jugendlichen (Mädchen und Jungen im Alter zwischen 12 Jahren und 17 Jahren) gedacht, wird allerdings meist von deren Mütter gekauft.
- Der Name des Autors lautet: Henrik Falbe
- Der Titel lautet: Junge Herzen finden Mut und Richtung
- Der Untertitel lautet: Was Heranwachsende über ihren Weg lernen
- Im Anhang befinden sich Designs, die ich gut finde (nur falls jemand weitere Ideen haben möchte)
- Format: 15,24 cm x 22,86 cm (6' x 9') [genaue Maße fürs Taschenbuch und Hardcover sind im Anhang (.zip Dateien)]
1. E-Book:
- Coverdateien sollten idealerweise 2 560 Pixel hoch und 1 600 Pixel breit sein. Zur Gewährleistung der bestmöglichen Qualität (insbesondere auf HD-Geräten) sollte das Bild mindestens 2 500 Pixel hoch sein.
- Format: TIFF (.tif/.tiff) oder JPEG (.jpeg/.jpg)
- DPI: 72 dpi
- Größe: Ihr Coverbild muss kleiner als 50 MB sein.
Hinweis: Vermeiden Sie es, Ihre Dateien zu komprimieren. Dies kann die Qualität Ihres Covers auf Lesegeräten beeinträchtigen. Das beste Ergebnis erzielen Sie mit Bildern, die eine Mindestauflösung von 300 ppi (Pixels per Inch) haben.
- Rahmen: Coverbilder mit weißem oder sehr hellem Hintergrund heben sich kaum vom weißen Hintergrund ab. Fügen Sie einen dünnen Rahmen (3–4 Pixel) in Mittelgrau hinzu, um die Ränder des Covers besser sichtbar zu machen.
2. + 3. Taschenbuch/Hardcover [genaue Maße fürs Taschenbuch und Hardcover sind im Anhang (.zip Dateien)] :
- Dateityp: Das Cover muss als einzelne PDF-Datei vorliegen und die hintere Coverseite, den Buchrücken und die vordere Coverseite als einzelnes Bild enthalten.
- Dateigröße: Coverdateien, die größer als 650 MB sind, können nicht konvertiert werden. Die Datei sollte maximal 40 MB groß sein, da sich bei großen Dateien der Druck verlangsamt.
- Die gen..

```html
<!DOCTYPE html>
<html lang="de">
<head>
<meta charset="utf-8">
<title>Junge Herzen finden Mut und Richtung – Henrik Falbe</title>
<link rel="stylesheet" href="https://fonts.googleapis.com/css2?family=Lexend:wght@400;500;700&display=swap">
<style>
  :root {
    --stage-green: #4aa22f;
    --title-green: #3a8c2e;
    --author-gold: #a68a1f;
    --subtitle-red: #c8102e;
    --shirt-red: #e0191c;
    --skin-tone: #f3b992;
    --pastel-blue: #bfe2ee;
    --pastel-pink: #f8e4ea;
    --pastel-mint: #d6ecd9;
    --pastel-cream: #fbf6d6;
  }
  html, body {
    margin: 0;
    padding: 0;
    width: 1200px;
    height: 1200px;
    overflow: hidden;
    background: var(--stage-green);
    font-family: "Lexend", sans-serif;
  }
  .book-cover {
    position: absolute;
    left: 224px;
    top: 57px;
    width: 763px;
    height: 1079px;
    overflow: hidden;
    background: #ffffff;
  }
  .cover-pattern {
    position: absolute;
    inset: 0;
    background:
      radial-gradient(ellipse 45% 30% at 55% 28%, #ffffff 0%, rgba(255,255,255,0) 100%),
      radial-gradient(ellipse 40% 35% at 0% 10%, var(--pastel-pink) 0%, rgba(248,228,234,0) 100%),
      radial-gradient(ellipse 35% 40% at 100% 25%, var(--pastel-cream) 0%, rgba(251,246,214,0) 100%),
      radial-gradient(ellipse 40% 45% at 90% 55%, var(--pastel-mint) 0%, rgba(214,236,217,0) 100%),
      radial-gradient(ellipse 55% 70% at 0% 75%, var(--pastel-blue) 0%, rgba(191,226,238,0) 100%),
      linear-gradient(160deg, var(--pastel-pink) 0%, #f4f8f2 35%, #eef6f4 60%, var(--pastel-blue) 100%);
  }
  .cover-illustration {
    position: absolute;
    left: 0;
    top: 440px;
    width: 763px;
    height: 639px;
    background:
      radial-gradient(ellipse 32% 22% at 76% 32%, var(--skin-tone) 0%, rgba(243,185,146,0) 100%),
      radial-gradient(ellipse 55% 55% at 92% 82%, var(--shirt-red) 0%, var(--shirt-red) 55%, rgba(224,25,28,0) 100%),
      radial-gradient(ellipse 30% 45% at 40% 62%, rgba(58,140,46,0.55) 0%, rgba(58,140,46,0) 100%),
      radial-gradient(ellipse 60% 70% at 15% 70%, var(--pastel-blue) 0%, rgba(191,226,238,0) 100%);
    -webkit-mask-image: linear-gradient(to bottom, transparent 0%, #000 28%);
    mask-image: linear-gradient(to bottom, transparent 0%, #000 28%);
  }
  .author {
    position: absolute;
    top: 34px;
    left: 0;
    width: 100%;
    margin: 0;
    text-align: center;
    font-weight: 400;
    font-size: 60px;
    letter-spacing: 3px;
    line-height: 1.2;
    color: var(--author-gold);
    text-transform: uppercase;
  }
  .title {
    position: absolute;
    top: 126px;
    left: 0;
    width: 100%;
    margin: 0;
    text-align: center;
    font-weight: 500;
    font-size: 76px;
    line-height: 81px;
    color: var(--title-green);
  }
  .subtitle {
    position: absolute;
    top: 381px;
    left: 0;
    width: 100%;
    margin: 0;
    text-align: center;
    font-weight: 700;
    font-size: 22px;
    line-height: 32px;
    letter-spacing: 0.5px;
    color: var(--subtitle-red);
  }
</style>
</head>
<body>
  <main class="book-cover">
    <div class="cover-pattern" role="img" aria-label="Pastellfarbener Hintergrund mit Flecken, Wellen und diagonalen Lichtstreifen"></div>
    <div class="cover-illustration" role="img" aria-label="Illustration: Jugendliche Person im roten Pullover mit Kleeblatt hält einen großen grünen Schlüssel mit Kleeblatt-Griff, auf dem ein Marienkäfer sitzt"></div>
    <p class="author">Henrik Falbe</p>
    <h1 class="title">Junge Herzen<br>finden Mut und<br>Richtung</h1>
    <p class="subtitle">Was Heranwachsende über<br>ihren Weg lernen</p>
  </main>
</body>
</html>
```